Need Flyer for Our Real estate Agency

Need to run General Campaign for our agency with Start of New Year as our theme ..Must have an agent's picture on the DL..
Address:
27 / 486Brindle rd, Marsden VIC 3047
Ph:03 9412 7306
email:info@kovalinrealestate.com.au
www.kovalinrealestate.com.au
Something like as attached picture..
Target Market(s)
Home Buyers
Industry/Entity Type
Real Estate Agent
Requirements
Must have
- Our Logo Colours

```html
<!DOCTYPE html>
<html lang="en">
<head>
<meta charset="utf-8">
<title>Kovalin Real Estate – New Year DL Flyer</title>
<link rel="stylesheet" href="https://fonts.googleapis.com/css2?family=Lato:wght@300;400;700&family=Source+Sans+3:wght@400;600;700&display=swap">
<style>
  :root {
    --page-bg: #e8e9ea;
    --navy: #0f2a68;
    --navy-deep: #061a4f;
    --crimson: #74121b;
    --white: #ffffff;
    --swoosh: #d4d5d8;
    --shadow: rgba(0, 0, 0, 0.28);
  }
  * { box-sizing: border-box; margin: 0; padding: 0; }
  html, body {
    width: 1169px;
    height: 1200px;
    overflow: hidden;
    background: var(--page-bg);
  }
  .sheet { position: relative; width: 1169px; height: 1200px; }
  .dl-card {
    position: absolute;
    left: 51px;
    width: 1059px;
    height: 504px;
    box-shadow: 6px 12px 18px var(--shadow);
    overflow: hidden;
    color: var(--white);
    font-family: "Lato", sans-serif;
  }
  .dl-card--front { top: 32px; }
  .dl-card--back { top: 615px; }
  .card-art { position: absolute; inset: 0; width: 100%; height: 100%; display: block; }

  .brand {
    position: absolute;
    left: 530px;
    width: 480px;
    top: 110px;
    text-align: center;
    font-family: "Lato", sans-serif;
    font-weight: 400;
    letter-spacing: 6px;
    font-size: 58px;
    line-height: 1;
    color: var(--white);
  }
  .brand-sub {
    display: block;
    margin-top: 10px;
    font-size: 13px;
    letter-spacing: 4px;
  }

  .headline {
    position: absolute;
    left: 530px;
    width: 480px;
    top: 230px;
    text-align: center;
    font-weight: 300;
    font-size: 36px;
    line-height: 49px;
  }
  .subline {
    position: absolute;
    left: 480px;
    width: 580px;
    top: 351px;
    text-align: center;
    font-family: "Source Sans 3", sans-serif;
    font-size: 19px;
    text-transform: uppercase;
    letter-spacing: 0.2px;
  }
  .subline strong { font-weight: 700; }

  .call-pill {
    position: absolute;
    left: 570px;
    top: 407px;
    width: 400px;
    height: 51px;
    border-radius: 26px;
    background: var(--white);
    color: var(--crimson);
    font-family: "Source Sans 3", sans-serif;
    font-weight: 700;
    font-size: 25px;
    display: flex;
    align-items: center;
    justify-content: center;
    gap: 10px;
    box-shadow: 0 4px 8px rgba(0,0,0,0.35);
  }
  .call-pill svg { width: 24px; height: 24px; }
  .appraisal-note {
    position: absolute;
    left: 570px;
    width: 400px;
    top: 466px;
    text-align: center;
    font-size: 19px;
    font-weight: 400;
  }

  .agent-name {
    position: absolute;
    left: 607px;
    top: 238px;
    font-size: 23px;
    font-weight: 300;
  }
  .contact-list {
    position: absolute;
    left: 607px;
    top: 284px;
    list-style: none;
    font-size: 20px;
    font-weight: 300;
  }
  .contact-list li {
    display: flex;
    align-items: center;
    gap: 12px;
    height: 39px;
  }
  .contact-list svg { width: 20px; height: 20px; flex: none; }
  .office-address {
    position: absolute;
    left: 440px;
    width: 619px;
    top: 452px;
    text-align: center;
    font-size: 21px;
    font-weight: 300;
    letter-spacing: 0.2px;
  }
</style>
</head>
<body>
<main class="sheet">

  <!-- Front: new year appraisal offer -->
  <section class="dl-card dl-card--front">
    <svg class="card-art" viewBox="0 0 1059 504" preserveAspectRatio="none">
      <defs>
        <linearGradient id="navyPanel" x1="0" y1="0" x2="1" y2="1">
          <stop offset="0" stop-color="var(--navy)"/>
          <stop offset="1" stop-color="var(--navy-deep)"/>
        </linearGradient>
        <linearGradient id="agentPhotoTones" x1="0" y1="0" x2="0" y2="1">
          <stop offset="0" stop-color="#9bb3d3"/>
          <stop offset="0.45" stop-color="#6f7585"/>
          <stop offset="0.75" stop-color="#2e4a86"/>
          <stop offset="1" stop-color="#4d7a3a"/>
        </linearGradient>
        <linearGradient id="swooshFade" x1="0" y1="0" x2="1" y2="0">
          <stop offset="0" stop-color="var(--swoosh)"/>
          <stop offset="1" stop-color="#f4f4f5"/>
        </linearGradient>
      </defs>
      <rect width="1059" height="504" fill="url(#navyPanel)"/>
      <rect x="0" y="432" width="1059" height="72" fill="var(--crimson)"/>
      <rect x="0" y="427" width="1059" height="4" fill="var(--white)"/>
      <path d="M330 0 H440 C505 150 515 330 452 504 H415 C460 330 430 120 330 0 Z" fill="url(#swooshFade)"/>
      <path d="M430 0 H448 C512 150 522 330 462 504 H452 C515 330 505 150 430 0 Z" fill="var(--white)"/>
      <path role="img" aria-label="Photo of the agent in a blue suit standing in front of a lit two-storey family home" d="M0 0 H330 C430 120 460 330 415 504 H0 Z" fill="url(#agentPhotoTones)"/>
    </svg>

    <div class="brand">KOVALIN<span class="brand-sub">REAL ESTATE</span></div>

    <h1 class="headline">Curious to know what your<br>home is worth?</h1>
    <p class="subline">Start the new year with <strong>Arjun Mehra</strong> and find out!</p>

    <div class="call-pill">
      <span>CALL ME NOW!</span>
      <svg viewBox="0 0 24 24" aria-hidden="true">
        <circle cx="12" cy="12" r="10.5" fill="none" stroke="var(--crimson)" stroke-width="2"/>
        <path d="M8.3 6.8c.4-.4 1-.4 1.3 0l1.2 1.6c.3.4.3.9-.1 1.2l-.7.6c.6 1.3 1.6 2.3 2.9 2.9l.6-.7c.3-.4.8-.4 1.2-.1l1.6 1.2c.4.3.4.9 0 1.3l-.8.8c-.6.6-1.6.7-2.4.3-2.4-1.2-4.3-3.1-5.5-5.5-.4-.8-.3-1.8.3-2.4z" fill="var(--crimson)"/>
      </svg>
      <span>0412 583 906</span>
    </div>
    <p class="appraisal-note">For Free property Appraisal</p>
  </section>

  <!-- Back: agent contact details -->
  <section class="dl-card dl-card--back">
    <svg class="card-art" viewBox="0 0 1059 504" preserveAspectRatio="none">
      <defs>
        <linearGradient id="navyPanelBack" x1="0" y1="0" x2="1" y2="1">
          <stop offset="0" stop-color="var(--navy)"/>
          <stop offset="1" stop-color="var(--navy-deep)"/>
        </linearGradient>
        <linearGradient id="handsPhotoTones" x1="0" y1="0" x2="1" y2="1">
          <stop offset="0" stop-color="#c9a38c"/>
          <stop offset="0.45" stop-color="#c9544e"/>
          <stop offset="0.75" stop-color="#2f4058"/>
          <stop offset="1" stop-color="#1e2f48"/>
        </linearGradient>
        <linearGradient id="swooshFadeBack" x1="0" y1="0" x2="1" y2="0">
          <stop offset="0" stop-color="var(--swoosh)"/>
          <stop offset="1" stop-color="#f4f4f5"/>
        </linearGradient>
      </defs>
      <rect width="1059" height="504" fill="url(#navyPanelBack)"/>
      <rect x="0" y="432" width="1059" height="72" fill="var(--crimson)"/>
      <rect x="0" y="427" width="1059" height="4" fill="var(--white)"/>
      <path d="M330 0 H440 C505 150 515 330 452 504 H415 C460 330 430 120 330 0 Z" fill="url(#swooshFadeBack)"/>
      <path d="M430 0 H448 C512 150 522 330 462 504 H452 C515 330 505 150 430 0 Z" fill="var(--white)"/>
      <path role="img" aria-label="Photo of two hands sheltering a small red model house" d="M0 0 H330 C430 120 460 330 415 504 H0 Z" fill="url(#handsPhotoTones)"/>
    </svg>

    <div class="brand">KOVALIN<span class="brand-sub">REAL ESTATE</span></div>

    <p class="agent-name">Arjun Mehra, Director</p>
    <ul class="contact-list">
      <li>
        <svg viewBox="0 0 24 24" aria-hidden="true">
          <circle cx="12" cy="12" r="10.5" fill="none" stroke="var(--white)" stroke-width="2"/>
          <path d="M8.3 6.8c.4-.4 1-.4 1.3 0l1.2 1.6c.3.4.3.9-.1 1.2l-.7.6c.6 1.3 1.6 2.3 2.9 2.9l.6-.7c.3-.4.8-.4 1.2-.1l1.6 1.2c.4.3.4.9 0 1.3l-.8.8c-.6.6-1.6.7-2.4.3-2.4-1.2-4.3-3.1-5.5-5.5-.4-.8-.3-1.8.3-2.4z" fill="var(--white)"/>
        </svg>
        <span>03 9412 7306</span>
      </li>
      <li>
        <svg viewBox="0 0 24 24" aria-hidden="true">
          <circle cx="12" cy="12" r="11" fill="var(--white)"/>
          <rect x="6" y="8" width="12" height="8" rx="1" fill="var(--navy)"/>
          <path d="M6.5 8.5 12 12.5l5.5-4" fill="none" stroke="var(--white)" stroke-width="1.2"/>
        </svg>
        <span>arjun.mehra@kovalinrealestate.com.au</span>
      </li>
      <li>
        <svg viewBox="0 0 24 24" aria-hidden="true">
          <circle cx="12" cy="12" r="11" fill="var(--white)"/>
          <circle cx="12" cy="12" r="6.5" fill="none" stroke="var(--navy)" stroke-width="1.3"/>
          <ellipse cx="12" cy="12" rx="2.8" ry="6.5" fill="none" stroke="var(--navy)" stroke-width="1.1"/>
          <path d="M5.5 12h13M6.5 9h11M6.5 15h11" stroke="var(--navy)" stroke-width="1"/>
        </svg>
        <span>www.kovalinrealestate.com.au</span>
      </li>
    </ul>
    <p class="office-address">27/486 Brindle Rd Marsden, Victoria, Australia 3047</p>
  </section>

</main>
</body>
</html>
```